Bright bears day nursery qrp limited

we would like create a website that can be updated by us easily as we have regular changes to what we provide and need. we would like something that is classy but also appealing from a child's aspect. we would be looking to add our own logo and our kinderwatch logo both attached, if you guys can create it and we will work with the preferred choice to add all the text.
We would like the links to family pathways, kinderwatch report and our chatterbook feed on the front page

we are looking for a website for our childcare business we have 2 nurseries that we would like one website.
showing our opening hours, price list, policies etc as well as photos, description of our day, staff photos and their training accreditation's.

Target Market(s)

Families

Industry/Entity Type

Childcare

Number of Pages Required

5+ page

Font styles to use
Serif

Colors

Designer to choose colors to be used in the design.

Requirements
Must have
• links to social media and other websites, photographs, links to download registration forms etc, parents able to leave reviews. google maps link, job opportunities
Nice to have
• facilities to take payments

```html
<!DOCTYPE html>
<html lang="en">
<head>
<meta charset="utf-8">
<title>Bright bears day nursery qrp limited – Feedback &amp; Contact</title>
<link rel="stylesheet" href="https://fonts.googleapis.com/css2?family=Arimo:wght@400;700&display=swap">
<style>
  :root {
    --page-bg: #f5f5f5;
    --band-bg: #e9e8e8;
    --footer-bg: #3d3d3f;
    --green: #4e8d37;
    --orange: #e8843a;
    --field-bg: #f5f4f4;
    --field-border: #c9c9c9;
    --placeholder: #b5b5b5;
    --ink: #222222;
    --white: #ffffff;
    --badge-navy: #14286e;
    --badge-purple: #2b2266;
    --badge-gold: #f3b634;
    --map-base: #e6e1d9;
  }
  * { box-sizing: border-box; margin: 0; padding: 0; }
  html, body { width: 978px; height: 1200px; overflow: hidden; }
  body {
    position: relative;
    background: var(--page-bg);
    font-family: "Arimo", Arial, sans-serif;
    color: var(--ink);
  }
  .top-strip { position: absolute; left: 0; top: 0; width: 978px; height: 51px; background: var(--page-bg); }
  .top-strip::after {
    content: ""; position: absolute; left: 460px; top: 0; width: 60px; height: 1px; background: #cfcfcf;
  }
  .section-title {
    position: absolute; left: 0; width: 100%; text-align: center;
    color: var(--green); font-weight: 700; font-size: 26px; letter-spacing: 0.3px;
  }
  .feedback { position: absolute; left: 0; top: 51px; width: 978px; height: 476px; background: var(--band-bg); }
  .feedback .section-title { top: 27px; left: 9px; }
  .badge { position: absolute; border-radius: 0 16px 16px 0; }
  .badge-first { left: 215px; top: 196px; width: 114px; height: 114px; background: var(--badge-navy); }
  .badge-second { left: 342px; top: 199px; width: 133px; height: 111px; background: var(--badge-gold); border-radius: 0 18px 18px 0; }
  .badge-second::before {
    content: ""; position: absolute; left: 0; top: 0; width: 108px; height: 111px;
    background: var(--badge-purple); border-radius: 0 18px 18px 0;
  }
  .field {
    position: absolute; left: 530px; width: 242px;
    background: var(--field-bg); border: 1px solid var(--field-border);
    border-radius: 11px; box-shadow: 0 2px 2px rgba(0,0,0,0.18);
    color: var(--placeholder); font-size: 17px; padding-left: 15px;
  }
  .field-comment { top: 134px; height: 130px; padding-top: 6px; }
  .field-email { top: 282px; height: 40px; line-height: 38px; }
  .field-rating { top: 344px; height: 41px; line-height: 39px; display: flex; align-items: center; gap: 8px; }
  .field-rating svg { display: block; }
  .submit-button {
    position: absolute; left: 688px; top: 401px; width: 82px; height: 27px;
    background: var(--orange); color: var(--white); border-radius: 14px;
    font-weight: 700; font-size: 17px; text-align: center; line-height: 27px;
    box-shadow: 0 1px 2px rgba(0,0,0,0.25);
  }
  .contact { position: absolute; left: 0; top: 527px; width: 978px; height: 518px; background: var(--page-bg); }
  .contact .section-title { top: 38px; left: 0; }
  .map-area {
    position: absolute; left: 203px; top: 89px; width: 573px; height: 215px;
    background: linear-gradient(135deg, #e9e4dc 0%, var(--map-base) 55%, #ddd8cf 100%);
  }
  .address-card {
    position: absolute; left: 397px; top: 318px; width: 185px; height: 176px;
    background: var(--band-bg); border: 1px solid #c6c6c6; border-radius: 10px;
    box-shadow: 0 2px 2px rgba(0,0,0,0.15);
    text-align: center; font-size: 9px; line-height: 15px; padding-top: 8px;
  }
  .address-card h3 { font-size: 11px; font-weight: 700; text-decoration: underline; line-height: 16px; }
  .address-card .block + .block { margin-top: 14px; }
  .site-footer { position: absolute; left: 0; top: 1045px; width: 978px; height: 155px; background: var(--footer-bg); color: var(--white); }
  .quote {
    position: absolute; left: 206px; top: 29px; width: 540px;
    text-align: center; font-size: 19px; line-height: 28px;
  }
  .quote-author { position: absolute; left: 599px; top: 85px; font-size: 21px; }
  .back-to-top { position: absolute; left: 805px; top: 49px; }
</style>
</head>
<body>
  <div class="top-strip"></div>

  <section class="feedback">
    <h2 class="section-title">FEEDBACK</h2>
    <div class="badge badge-first" role="img" aria-label="kinderwatch outstanding award badge"></div>
    <div class="badge badge-second" role="img" aria-label="kinderwatch outstanding early years provider badge"></div>

    <div class="field field-comment">Comment...</div>
    <div class="field field-email">Email...</div>
    <div class="field field-rating">
      <span>Rate us:</span>
      <svg width="134" height="26" viewBox="0 0 134 26" aria-label="Three of five stars">
        <g stroke-width="2" stroke-linejoin="round" fill="none">
          <path id="star" d="M13 2 L16.2 9.6 L24.4 10.2 L18.1 15.5 L20.1 23.5 L13 19.2 L5.9 23.5 L7.9 15.5 L1.6 10.2 L9.8 9.6 Z" stroke="#4e8d37"/>
          <use href="#star" x="26"/>
          <use href="#star" x="52"/>
          <path d="M13 2 L16.2 9.6 L24.4 10.2 L18.1 15.5 L20.1 23.5 L13 19.2 L5.9 23.5 L7.9 15.5 L1.6 10.2 L9.8 9.6 Z" transform="translate(78 0)" stroke="#d3d3d3" stroke-width="1.4"/>
          <path d="M13 2 L16.2 9.6 L24.4 10.2 L18.1 15.5 L20.1 23.5 L13 19.2 L5.9 23.5 L7.9 15.5 L1.6 10.2 L9.8 9.6 Z" transform="translate(104 0)" stroke="#d3d3d3" stroke-width="1.4"/>
        </g>
      </svg>
    </div>
    <div class="submit-button">Submit</div>
  </section>

  <section class="contact">
    <h2 class="section-title">CONTACT US</h2>
    <div class="map-area" role="img" aria-label="Street map showing the nursery location"></div>
    <div class="address-card">
      <div class="block">
        <h3>Address</h3>
        <p>ur address goes here</p>
        <p>street,Alderton 0241</p>
      </div>
      <div class="block">
        <h3>Phone</h3>
        <p>+0123 4410 2286</p>
        <p>+0123 4410 2297</p>
      </div>
      <div class="block">
        <h3>Email</h3>
        <p>hello@brightbears.co</p>
      </div>
    </div>
  </section>

  <footer class="site-footer">
    <p class="quote">"Don't compare yourself with anyone in this world ... if you do so, you are insulting yourself."</p>
    <p class="quote-author">Marcus Ellery</p>
    <svg class="back-to-top" width="38" height="38" viewBox="0 0 38 38" aria-label="Back to top">
      <circle cx="19" cy="19" r="17.5" fill="#4a4a4c" stroke="#2a2a2a" stroke-width="1.5"/>
      <path d="M19 9 L28 18 L23 18 L23 28 L15 28 L15 18 L10 18 Z" fill="#e8843a" stroke-linejoin="round"/>
    </svg>
  </footer>
</body>
</html>
```